Website: BrightHarbor Business Consultants, Qianhai SEZ, China

Our client is a business consultancy firm and will be the first to set up in the Qianhai Shenzhen-Hong Kong Modern Service Industry Cooperation Zone, China So we need a corporate website concept that engages service, finance and technology sector companies. The company can provide all the necessary services needed to set up shop in Qianhai. They are looking for a modern, international, reliable and strong image.

Here are some websites for reference prupose:

http://www.vornelpax.com/ (we like the dynamic banner and clear, clean layout of this website)

http://www.quilbrenadvisory.com/ (we like the background city image, use of light font, hover over menu functions and color scheme - purple and grey)

http://www.dovu.com/ (we like the simplicity of this website, clear lines and we like the dynamic banner)
Updates

Hello, We are currently undecided between three logo designs.  All three have been uploaded to the design brief so that you can use them as reference for the website design. Thx

Also please take note of the addition menu selection 'About Qianhai'. Thx

Hello all Designers, First of all we want thank you for participating in our website competition, the calibre of design was high and we appreciated the expedience. Our company is Lumen Harvest Web Design and Internet Marketing based in Shenzhen, China. We anticipate rapid growth in the Chinese domestic market as the country shifts in to a service sector economy. We hope to continue building reliable working relationships with you based on idea sharing and constructive feedback. Once again, Thankyou, LH Team

Target Market(s)

International finance and technology companies looking to set up in Qianhai Special Economic Zone, China

Industry/Entity Type

Finance

Requirements
Must have
• Initial design for home page and in later selection stages a secondary page will be required.

The design should be for PSD concepts only no code!

Menu bar, Photo banner -
A. Photo banner and text overlay,
B.Photo Banner and text description to left or right.

Social Connect icons, Site search bar (top right), Logo space (top left).

Menu bar at top with Home, About Us, About Qianhai, Services, Portfolio, Partners, Our Team Contact Us.

Standard 3-4 box layout - Banner at top and 2-3 boxes under banner.

Colour scheme- A. Purple and Blue, must have light background/body
B. Shades of white, black and grey.

Simple, clear, clean, sharp.

```html
<!DOCTYPE html>
<html lang="en">
<head>
<meta charset="utf-8">
<title>BrightHarbor Business Consulting</title>
<link href="https://fonts.googleapis.com/css2?family=Arimo:wght@400;700&family=Cinzel:wght@600&family=Poiret+One&display=swap" rel="stylesheet">
<style>
:root{
  --ink:#2b2b2b;
  --text:#333;
  --muted:#6b6b6b;
  --line:#cfcfcf;
  --accent:#2f86c9;
  --panel:#2e2e2e;
  --footer:#333;
  --page:#fff;
  --chip:#e9e9e9;
}
*{box-sizing:border-box;margin:0;padding:0}
html,body{width:1120px;height:1200px;overflow:hidden;background:var(--page)}
body{font-family:Arimo,Arial,sans-serif;color:var(--text)}
.canvas{position:relative;width:1120px;height:1200px}
.abs{position:absolute}

.topbar{left:0;top:0;width:1120px;height:38px;border-bottom:1px solid var(--line)}
.social{right:106px;top:6px;display:flex;gap:6px}
.social a{display:flex;align-items:center;gap:3px;height:26px;padding:0 5px;background:var(--chip);border-radius:3px;font-size:10px;color:var(--ink);text-decoration:none}
.social a i{width:8px;height:8px;background:#888;display:block}

.brand{left:97px;top:58px;width:245px;text-align:center}
.brand-mark{width:46px;height:46px;border-radius:50%;background:var(--ink);margin:0 auto 8px}
.brand-name{font-family:Cinzel,serif;font-weight:600;font-size:27px;color:var(--ink);letter-spacing:.5px;line-height:1}
.brand-tag{font-family:Cinzel,serif;font-weight:600;font-size:10px;color:var(--ink);letter-spacing:8.4px;margin-top:4px}

.search{left:846px;top:67px;width:177px;height:23px;border:1px solid #bdbdbd;background:#f3f3f3;font-size:14px;color:#9a9a9a;padding:3px 0 0 25px}
.search .divider{position:absolute;left:133px;top:2px;width:1px;height:17px;background:#bdbdbd}
.search svg{position:absolute;left:148px;top:4px}

.nav{left:351px;top:118px;width:674px;height:55px;border:1px solid #ddd;background:#fafafa;display:flex;align-items:center;padding-left:11px;font-size:13.5px}
.nav a{color:var(--text);text-decoration:none}
.nav a.current{color:var(--accent)}
.nav .sep{color:#aaa;margin:0 12px}

.slider{left:92px;top:208px;width:936px;height:400px;border:1px solid #d6d6d6;padding:3px}
.slide{position:relative;width:100%;height:100%;background:linear-gradient(180deg,#0b0b1a 0%,#1c1830 45%,#3a2a3a 72%,#0f1420 100%)}
.slide-copy{position:absolute;left:0;top:0;width:300px;height:100%;background:rgba(40,40,40,.85);padding:22px 0 0 33px;color:#fff}
.arrows{display:flex;gap:10px;margin-bottom:40px}
.slide-copy h2{font-size:23px;line-height:24px;font-weight:700;width:240px}
.slide-copy .lede{font-size:14px;line-height:16px;color:#ccc;margin-top:20px;width:235px}
.slide-copy .note{position:absolute;left:33px;top:303px;font-size:10.5px;line-height:13px;color:#bbb;width:250px}

.tagline{left:0;top:618px;width:1120px;text-align:center}
.tagline h1{font-family:"Poiret One",sans-serif;font-weight:400;font-size:30px;color:var(--ink);letter-spacing:.5px}
.tagline p{font-size:15.5px;color:var(--muted);margin-top:5px;letter-spacing:.4px}

.rule{left:0;width:1120px;height:1px;background:var(--line)}
.section-title{display:flex;align-items:center;gap:14px;font-family:"Poiret One",sans-serif;font-size:21px;color:var(--ink)}
.section-title svg{flex:none}

.card{top:744px;width:222px;height:241px;border:1px solid #d6d6d6;background:#fff}
.card .photo{margin:3px;height:174px}
.card .caption{position:absolute;left:-1px;right:-1px;bottom:-1px;height:58px;background:var(--panel);color:#e8e8e8;font-size:11.5px;line-height:13px;padding:3px 16px 0 28px;text-align:justify}
.card .more{display:inline-block;margin-top:6px;background:#d9d9d9;color:#333;border:1px solid #999;font-size:11px;padding:1px 4px}

.vline{top:1044px;width:1px;height:56px;background:var(--line)}
.client{top:1044px;width:108px;height:56px;border:1px solid #cfcfcf;display:flex;align-items:center;justify-content:center;gap:5px;font-size:13px;font-weight:700;color:#222}
.client i{width:9px;height:9px;background:#222;display:block}

.footer{left:0;top:1127px;width:1120px;height:73px;background:var(--footer);color:#e6e6e6;font-size:11.5px;text-align:center}
.footer nav{padding-top:15px}
.footer nav a{color:#e6e6e6;text-decoration:none}
.footer nav .sep{color:#888;margin:0 16px}
.footer .copy{margin-top:19px}
</style>
</head>
<body>
<div class="canvas">

  <header>
    <div class="abs topbar"></div>
    <div class="abs social">
      <a href="#"><i></i>Linkwave</a>
      <a href="#"><i></i>Chirpline</a>
      <a href="#"><i></i>Circlo</a>
      <a href="#"><i></i>Snapbank</a>
      <a href="#"><i></i>Pinora</a>
    </div>

    <div class="abs brand">
      <div class="brand-mark"></div>
      <div class="brand-name">BRIGHTHARBOR</div>
      <div class="brand-tag">BUSINESS CONSULTING</div>
    </div>

    <div class="abs search">search
      <span class="divider"></span>
      <svg width="15" height="13" viewBox="0 0 15 13"><circle cx="5" cy="5" r="3.6" fill="none" stroke="#999" stroke-width="1.6"/><line x1="7.8" y1="7.6" x2="13" y2="11.5" stroke="#999" stroke-width="2"/></svg>
    </div>

    <nav class="abs nav">
      <a class="current" href="#">Home</a><span class="sep">/</span>
      <a href="#">About Us</a><span class="sep">/</span>
      <a href="#">About Qianhai</a><span class="sep">/</span>
      <a href="#">Services</a><span class="sep">/</span>
      <a href="#">Portfolio</a><span class="sep">/</span>
      <a href="#">Partners</a><span class="sep">/</span>
      <a href="#">Our Team</a><span class="sep">/</span>
      <a href="#">contact Us</a>
    </nav>
  </header>

  <section class="abs slider">
    <div class="slide" role="img" aria-label="Night skyline of a harbour city with lit towers and light beams over the water">
      <div class="slide-copy">
        <div class="arrows">
          <svg width="10" height="14" viewBox="0 0 10 14"><path d="M8 1 2 7l6 6" fill="none" stroke="#ddd" stroke-width="2.4"/></svg>
          <svg width="10" height="14" viewBox="0 0 10 14"><path d="M2 1l6 6-6 6" fill="none" stroke="#ddd" stroke-width="2.4"/></svg>
        </div>
        <h2>Nemo enim ipsam voluptatem quia voluptas sit</h2>
        <p class="lede">sed quia consequuntur magni eos qui ratione voluptatem sequi nesciunt.</p>
        <p class="note">eaque ipsa quae ab illo inventore veritatis et quasi architecto beatae vitae dicta sunt explicabo.</p>
      </div>
    </div>
  </section>

  <div class="abs tagline">
    <h1>Sed ut perspiciatis unde omnis iste natus error sit</h1>
    <p>laudantium, totam rem aperiam</p>
  </div>

  <div class="abs rule" style="top:696px"></div>

  <section>
    <h3 class="abs section-title" style="left:95px;top:707px">
      <svg width="11" height="16" viewBox="0 0 11 16"><path d="M0 0l11 8-11 8z" fill="#222"/></svg>Lorem Ipsum
    </h3>

    <article class="abs card" style="left:95px">
      <div class="photo" role="img" aria-label="Close-up of a hand adjusting a wristwatch on a shirt cuff" style="background:linear-gradient(135deg,#e8dcd4,#c9a78f 60%,#b9b2ad)"></div>
      <div class="caption">Lorem ipsum dolor sit amet, consectetur adipisicing elit...<br><span class="more">Read More</span></div>
    </article>
    <article class="abs card" style="left:332px">
      <div class="photo" role="img" aria-label="Business team in an office with a woman holding folders in front" style="background:linear-gradient(135deg,#9fb6cc,#3d4a5c 55%,#1d2430)"></div>
      <div class="caption">Lorem ipsum dolor sit amet, consectetur adipisicing elit...<br><span class="more">Read More</span></div>
    </article>
    <article class="abs card" style="left:569px">
      <div class="photo" role="img" aria-label="Businessman in a suit standing in front of high-rise towers" style="background:linear-gradient(180deg,#c9d3dc,#8f9aa4 60%,#4e5760)"></div>
      <div class="caption">Lorem ipsum dolor sit amet, consectetur adipisicing elit...<br><span class="more">Read More</span></div>
    </article>
    <article class="abs card" style="left:805px">
      <div class="photo" role="img" aria-label="Hand typing on a laptop keyboard" style="background:linear-gradient(135deg,#f4f4f4,#9a9a9a 55%,#3a3a3a)"></div>
      <div class="caption">Lorem ipsum dolor sit amet, consectetur adipisicing elit...<br><span class="more">Read More</span></div>
    </article>
  </section>

  <div class="abs rule" style="top:1016px"></div>

  <section>
    <h3 class="abs section-title" style="left:95px;top:1060px">
      <svg width="11" height="16" viewBox="0 0 11 16"><path d="M0 0l11 8-11 8z" fill="#222"/></svg>Our Clients
    </h3>
    <div class="abs vline" style="left:313px"></div>
    <div class="abs client" style="left:344px"><i></i>Norvalix</div>
    <div class="abs client" style="left:483px"><i></i>Fizzmont</div>
    <div class="abs client" style="left:621px"><i></i>Qorvane</div>
    <div class="abs client" style="left:759px"><i></i>Tallyframe</div>
    <div class="abs vline" style="left:899px"></div>
  </section>

  <footer class="abs footer">
    <nav>
      <a href="#">Home</a><span class="sep">|</span>
      <a href="#">About Us</a><span class="sep">|</span>
      <a href="#">About Qianhai</a><span class="sep">|</span>
      <a href="#">Services</a><span class="sep">|</span>
      <a href="#">Portfolio</a><span class="sep">|</span>
      <a href="#">Partners</a><span class="sep">|</span>
      <a href="#">Our Team</a><span class="sep">|</span>
      <a href="#">Contact Us</a>
    </nav>
    <p class="copy">copyright &copy; 2013 BrightHarbor. All Rights Reserved</p>
  </footer>

</div>
</body>
</html>
```